Create a new dynamic Video Production company website

A new website for a video production company. It needs to be focused on the videos with an easy to use and versatile video player. I want to be able to update (add/remove/edit) the videos myself and change some other regular information like price lists. Current website is www.reelvanta.ca
The new pages will be - Home - Corporate - Ministry - Wedding - Events - Contact

I was asked about Wordpress - I am not against WordPress so long as the designing company sets everything up properly. I have had bad experiences with Wordpress security (and spam) so as long as those issues are addressed, I can work with Wordpress.

Coding

Coded - Design and coding required

Number of Pages Required

5+ page

Requirements
Must have
• Video player that scales to different platforms - computers, tablets, cell phones etc.

```html
<!DOCTYPE html>
<html lang="en">
<head>
<meta charset="utf-8">
<title>Reelvanta — Video Production</title>
<link href="https://fonts.googleapis.com/css2?family=Roboto+Slab:wght@300;400;700&family=Open+Sans:wght@400;600&display=swap" rel="stylesheet">
<style>
:root{
  --gold:#e2c070;
  --gold-band:#dcbd78;
  --brown:#7b5c3c;
  --dark:#16181e;
  --ink:#2b2b2b;
  --text:#555;
  --muted:#f6f6f6;
  --white:#fff;
}
*{box-sizing:border-box;margin:0;padding:0}
html,body{width:1200px;height:2826px;overflow:hidden}
body{position:relative;background:var(--white);font-family:"Open Sans",Arial,sans-serif;color:var(--text)}
h1,h2,h3{font-weight:400}
.abs{position:absolute}

/* header */
.site-header{left:0;top:0;width:1200px;height:94px;background:var(--white);border-top:3px solid var(--gold)}
.brand{left:85px;top:22px;display:flex;align-items:center;gap:10px}
.brand-dot{width:40px;height:40px;border-radius:50%;background:var(--ink)}
.brand-name{font-family:"Roboto Slab",Georgia,serif;font-weight:700;font-size:30px;color:var(--ink);letter-spacing:1px}
.main-nav a{position:absolute;top:40px;font-family:"Roboto Slab",Georgia,serif;font-size:12px;color:#333;text-decoration:none;letter-spacing:.5px}

/* hero */
.hero{left:0;top:94px;width:1200px;height:588px;background:linear-gradient(160deg,#5a5a5a 0%,#2a2a2a 45%,#161616 100%)}
.hero-title{left:0;width:1200px;top:286px;text-align:center;font-family:"Roboto Slab",Georgia,serif;font-weight:700;font-size:62px;color:var(--gold);letter-spacing:2px}
.hero-text{left:245px;width:710px;top:374px;text-align:center;font-family:Arial,sans-serif;font-size:12.5px;line-height:28px;color:var(--white)}
.btn-gold{display:flex;align-items:center;justify-content:center;background:var(--gold);color:var(--white);font-family:"Roboto Slab",Georgia,serif;font-size:16px;letter-spacing:.5px}
.hero-btn{left:522px;top:450px;width:156px;height:51px}
.hero-arrow{top:362px;width:52px;height:52px;border:2px solid var(--white);border-radius:50%;display:flex;align-items:center;justify-content:center}

/* section heads */
.section-title{left:0;width:1200px;text-align:center;font-family:"Roboto Slab",Georgia,serif;font-weight:300;font-size:27px;color:var(--gold);letter-spacing:1px}
.section-sub{left:0;width:1200px;text-align:center;font-family:Arial,sans-serif;font-size:12px;color:#555}

/* services */
.services{left:0;top:682px;width:1200px;height:426px;background:var(--muted)}
.service{width:243px}
.service-photo{width:243px;height:164px}
.service-name{margin-top:16px;text-align:center;font-family:"Roboto Slab",Georgia,serif;font-size:20px;color:#333}
.service-desc{margin-top:6px;text-align:center;font-family:Arial,sans-serif;font-size:12px;line-height:25px;color:#555}

/* about */
.about-title{left:87px;top:1150px;font-family:"Roboto Slab",Georgia,serif;font-weight:300;font-size:27px;color:var(--gold);letter-spacing:1px}
.about-text{left:87px;top:1202px;width:475px;font-family:Arial,sans-serif;font-size:12.5px;line-height:26px;color:#555}
.about-text p+p{margin-top:16px}
.about-btn{left:87px;top:1426px;width:120px;height:40px;font-size:15px}
.about-photo{left:624px;top:1155px;width:489px;height:301px;background:linear-gradient(135deg,#6f8796 0%,#3c4a55 55%,#24292f 100%)}

/* events */
.events{left:0;top:1513px;width:1200px;height:373px;background:linear-gradient(120deg,#d8b56a 0%,var(--gold-band) 50%,#c9a863 100%)}
.events-title{left:0;width:1200px;top:1600px;text-align:center;font-family:"Roboto Slab",Georgia,serif;font-size:27px;color:var(--white);letter-spacing:1px}
.events-text{left:207px;width:786px;top:1652px;text-align:center;font-family:Arial,sans-serif;font-size:12px;line-height:27px;color:var(--white)}
.events-btn{left:465px;top:1765px;width:268px;height:49px;border:2px solid rgba(255,255,255,.8);display:flex;align-items:center;justify-content:center;color:var(--white);font-family:Arial,sans-serif;font-weight:700;font-size:14px}

/* pricing */
.pricing{left:0;top:1886px;width:1200px;height:704px;background:var(--muted)}
.plan{background:var(--white);border:1px solid #e6e6e6;box-shadow:0 2px 10px rgba(0,0,0,.08);text-align:center}
.plan-dot{position:absolute;left:50%;top:-11px;width:16px;height:16px;margin-left:-11px;border-radius:50%;background:var(--brown);border:3px solid var(--white);box-sizing:content-box}
.plan-name{margin-top:26px;font-family:"Roboto Slab",Georgia,serif;font-size:17px;letter-spacing:1px;color:#222}
.plan-price{margin:14px auto 0;width:114px;height:114px;border-radius:50%;background:var(--brown);color:var(--white);display:flex;flex-direction:column;align-items:center;justify-content:center;font-family:Arial,sans-serif}
.plan-price b{font-weight:700;font-size:26px;line-height:30px}
.plan-price span{font-size:12px;font-weight:700;letter-spacing:.5px}
.plan-features{list-style:none;margin:14px 10px 0}
.plan-features li{font-family:Arial,sans-serif;font-size:11.5px;color:#444;height:43px;line-height:43px;white-space:nowrap;border-bottom:1px solid #ececec}
.plan-features li:last-child{border-bottom:none}
.plan-btn{margin:12px auto 0;width:115px;height:42px;background:var(--brown);color:var(--white);display:flex;align-items:center;justify-content:center;font-family:"Roboto Slab",Georgia,serif;font-size:15px}
.plan.featured .plan-dot,.plan.featured .plan-price,.plan.featured .plan-btn{background:var(--gold)}

/* footer */
.footer-rule{left:0;top:2590px;width:1200px;height:6px;background:var(--gold)}
.site-footer{left:0;top:2596px;width:1200px;height:230px;background:var(--dark)}
.social{top:2618px;width:58px;height:58px;border:1px solid #3a3c44;border-radius:50%;display:flex;align-items:center;justify-content:center}
.social-mark{width:12px;height:12px;background:var(--white)}
.footer-line{left:120px;top:2702px;width:1025px;height:1px;background:#30323a}
.footer-nav{left:0;width:1200px;top:2722px;text-align:center;font-family:"Roboto Slab",Georgia,serif;font-size:12px;color:#ddd;letter-spacing:.5px}
.footer-nav span{margin:0 22px;color:#888}
.copyright{left:0;width:1200px;top:2765px;text-align:center;font-family:Arial,sans-serif;font-size:12px;color:#ccc}
</style>
</head>
<body>

<header class="abs site-header">
  <div class="abs brand"><span class="brand-dot"></span><span class="brand-name">REELVANTA</span></div>
  <nav class="main-nav">
    <a style="left:577px">HOME</a>
    <a style="left:655px">CORPORATE</a>
    <a style="left:768px">MINISTRY</a>
    <a style="left:869px">WEDDING</a>
    <a style="left:968px">EVENTS</a>
    <a style="left:1058px">CONTACT</a>
  </nav>
</header>

<section class="abs hero" role="img" aria-label="Film crew silhouetted in a dark studio with lights and camera rig"></section>
<div class="abs hero-arrow" style="left:23px"><svg width="20" height="20" viewBox="0 0 20 20"><path d="M13 3 L6 10 L13 17" fill="none" stroke="#fff" stroke-width="2.5"/></svg></div>
<div class="abs hero-arrow" style="left:1122px"><svg width="20" height="20" viewBox="0 0 20 20"><path d="M7 3 L14 10 L7 17" fill="none" stroke="#fff" stroke-width="2.5"/></svg></div>
<h1 class="abs hero-title">REELVANTA</h1>
<p class="abs hero-text">Live Sermons, Teaching Videos, Promotional video, and Special Services are just a few of the places where video productions can enhance your ministry. We are a Christian organization so all the work we do is from a Faith</p>
<div class="abs btn-gold hero-btn">READ MORE</div>

<section class="abs services"></section>
<h2 class="abs section-title" style="top:712px">OUR SERVICES</h2>
<p class="abs section-sub" style="top:757px">Live Sermons, Teaching Videos, Promotional video, and Special Services are just a few of the places where video productions</p>
<div class="abs service" style="left:87px;top:806px">
  <div class="service-photo" role="img" aria-label="Band performing live on a church stage" style="background:linear-gradient(160deg,#4c6e95,#1f2e44)"></div>
  <h3 class="service-name">Live Sermons</h3>
  <p class="service-desc">You can have your teaching at a live event or pecifically for just recording the video</p>
</div>
<div class="abs service" style="left:349px;top:806px">
  <div class="service-photo" role="img" aria-label="Studio set with lights and crew filming" style="background:linear-gradient(160deg,#6b5a48,#1e1a17)"></div>
  <h3 class="service-name">Instructional Video</h3>
  <p class="service-desc">You can have your teaching at a live event or pecifically for just recording the video</p>
</div>
<div class="abs service" style="left:609px;top:806px">
  <div class="service-photo" role="img" aria-label="Camera on a handheld gimbal stabilizer outdoors" style="background:linear-gradient(160deg,#b8bcc2,#4b4f56)"></div>
  <h3 class="service-name">Videos for Service</h3>
  <p class="service-desc">You can have your teaching at a live event or pecifically for just recording the video</p>
</div>
<div class="abs service" style="left:870px;top:806px">
  <div class="service-photo" role="img" aria-label="Editor working at a multi-screen video control desk" style="background:linear-gradient(160deg,#3b5470,#141a22)"></div>
  <h3 class="service-name">Promotional Video</h3>
  <p class="service-desc">You can have your teaching at a live event or pecifically for just recording the video</p>
</div>

<h2 class="abs about-title">ABOUT REELVANTA</h2>
<div class="abs about-text">
  <p>Live Sermons, Teaching Videos, Promotional video, and Special Services are just a few of the places where video productions can enhance your ministry. We are a Christian organization so all the work we do is from a Faith based perspective. All our productions are done with 2 or more professional cameras</p>
  <p>The Disc and case will also be specially designed for you and reflect the essence of the message. In 2005, we produced a Mother's Day video at Harbourview Gospel Centre involving all the children.The children spoke poems, special words</p>
</div>
<div class="abs btn-gold about-btn">READ MORE</div>
<div class="abs about-photo" role="img" aria-label="Videographer holding a camera and checking its screen"></div>

<section class="abs events" role="img" aria-label="Gold-toned backdrop of a camera operator at work"></section>
<h2 class="abs events-title">UPCOMING EVENTS</h2>
<p class="abs events-text">Any Special Event is worth remembering. Whether it's a Birthday Party, Anniversary, Graduation, Recitals or any other special occasions, you don't just have to remember it, you can relive it! Video Productions capture the essence of the moment and all the events that took place on your special to music of your choice. These productions are a pleasure to watch over and over again</p>
<div class="abs events-btn">CLICK HERE FOR MORE INFO</div>

<section class="abs pricing"></section>
<h2 class="abs section-title" style="top:1938px">PRICING PLAN</h2>
<p class="abs section-sub" style="top:1985px">Live Sermons, Teaching Videos, Promotional video, and Special Services are just a few of the places where video productions</p>

<div class="abs plan" style="left:196px;top:2082px;width:254px;height:429px">
  <span class="plan-dot"></span>
  <h3 class="plan-name">STANDARD PLAN</h3>
  <div class="plan-price"><b>$7.99</b><span>MONTHLY</span></div>
  <ul class="plan-features"><li>Sed ut perspiciatis unde omnis iste</li><li>natus error sit voluptatem accusantium</li><li>doloremque laudantium, totam rem</li><li>aperiam, eaque ipsa quae ab illo</li></ul>
  <div class="plan-btn">SIGN UP</div>
</div>
<div class="abs plan" style="left:763px;top:2082px;width:245px;height:429px">
  <span class="plan-dot"></span>
  <h3 class="plan-name">ULTIMATE PLAN</h3>
  <div class="plan-price"><b>$25.96</b><span>MONTHLY</span></div>
  <ul class="plan-features"><li>Sed ut perspiciatis unde omnis iste</li><li>natus error sit voluptatem accusantium</li><li>doloremque laudantium, totam rem</li><li>aperiam, eaque ipsa quae ab illo</li></ul>
  <div class="plan-btn">SIGN UP</div>
</div>
<div class="abs plan featured" style="left:450px;top:2057px;width:314px;height:477px">
  <span class="plan-dot"></span>
  <h3 class="plan-name" style="margin-top:50px">PREMIUM PLAN</h3>
  <div class="plan-price"><b>$20.97</b><span>MONTHLY</span></div>
  <ul class="plan-features" style="margin:24px 18px 0"><li>Sed ut perspiciatis unde omnis iste</li><li>natus error sit voluptatem accusantium</li><li>doloremque laudantium, totam rem</li><li>aperiam, eaque ipsa quae ab illo</li></ul>
  <div class="plan-btn">SIGN UP</div>
</div>

<div class="abs footer-rule"></div>
<footer class="abs site-footer"></footer>
<span class="abs social" style="left:425px"><span class="social-mark"></span></span>
<span class="abs social" style="left:498px"><span class="social-mark"></span></span>
<span class="abs social" style="left:568px"><span class="social-mark"></span></span>
<span class="abs social" style="left:641px"><span class="social-mark"></span></span>
<span class="abs social" style="left:711px"><span class="social-mark"></span></span>
<span class="abs social" style="left:783px"><svg width="16" height="12" viewBox="0 0 16 12"><rect x="1" y="1" width="14" height="10" fill="none" stroke="#fff" stroke-width="1.5"/><path d="M1 1 L8 7 L15 1" fill="none" stroke="#fff" stroke-width="1.5"/></svg></span>
<div class="abs footer-line"></div>
<nav class="abs footer-nav">HOME<span>|</span>CORPORATE<span>|</span>MINISTRY<span>|</span>WEDDING<span>|</span>EVENTS<span>|</span>CONTACT</nav>
<p class="abs copyright">© Copyrights 2017 Reelvanta.All Rights Reseved</p>

</body>
</html>
```